Construction material supplies company business card ****

1. Full company name “K T Masonry Works Ltd”
I am after a Business card design for the company as a whole. We are better known in Solomon Islands as “K T Masonry” for short.

We are a building materials supplier of
Ready Mixed Concrete, Bricks and Blocks,
Quarry products- gravel, aggregates, sand etc.
Cement distributor/retailer of reputable brands.
Other prefab concrete products. Culverts, wave breakers, concrete retaining blocks etc.

2. Competitive Advantage over Competition: Quality, efficient, professional, dependable, reliable

3. We want people to feel trust worthy, high quality, strong when they see our brand

5. No preference to color. Maybe more sturdy and corporate. Not fancy.

Industry/Entity Type

CONSTRUCTION SUPPLY

Contact Information for Business Card

Name, Position, office phone mob phone, email

Requirements
Must have
• the company logo
Nice to have
• would like to see a mixture of designs, of with logo only and also with simple graphic designs to bring out the company whilst still have the strong sturdy professional feeling

```html
<!DOCTYPE html>
<html lang="en">
<head>
<meta charset="utf-8">
<title>K T Masonry Business Card</title>
<link rel="stylesheet" href="https://fonts.googleapis.com/css2?family=Orbitron:wght@600&family=Open+Sans:wght@400;600&display=swap">
<style>
  :root {
    --navy: #12436a;
    --white: #ffffff;
    --backdrop: #9c9c9c;
    --ink: #1e2a36;
  }
  * { margin: 0; padding: 0; box-sizing: border-box; }
  html, body { width: 1132px; height: 1200px; overflow: hidden; }
  body { background: var(--backdrop); position: relative; font-family: "Open Sans", sans-serif; }

  .card { position: absolute; left: 215px; width: 701px; height: 401px; overflow: hidden; }
  .card-front { top: 151px; background: var(--navy); }
  .card-back { top: 648px; background: var(--white); }

  .brand-mark { display: block; }
  .brand-name { font-family: "Orbitron", sans-serif; font-weight: 600; white-space: nowrap; letter-spacing: 1px; }

  .front-lockup { position: absolute; left: 0; right: 0; top: 136px; display: flex; flex-direction: column; align-items: center; gap: 22px; }
  .front-lockup .brand-mark { width: 58px; height: 58px; background: var(--white); }
  .front-lockup .brand-name { color: var(--white); font-size: 38px; line-height: 1; }

  .back-lockup { position: absolute; left: 0; right: 0; top: 106px; display: flex; justify-content: center; align-items: center; gap: 18px; }
  .back-lockup .brand-mark { width: 48px; height: 48px; background: var(--navy); }
  .back-lockup .brand-name { color: var(--navy); font-size: 32px; line-height: 1; }

  .person { position: absolute; right: 354px; top: 254px; text-align: right; }
  .person-name { font-family: "Orbitron", sans-serif; font-weight: 600; color: var(--navy); font-size: 19px; letter-spacing: 1px; line-height: 1.2; margin-bottom: 4px; }
  .person-role, .person-company { font-size: 13.5px; color: var(--ink); line-height: 20px; }

  .divider { position: absolute; left: 362px; top: 256px; width: 1.5px; height: 56px; background: var(--ink); }

  .contacts { position: absolute; left: 385px; top: 254px; list-style: none; }
  .contacts li { display: flex; align-items: center; gap: 9px; font-size: 14px; color: var(--ink); line-height: 20px; }
  .contacts svg { width: 12px; height: 12px; fill: var(--navy); flex: none; }

  .footer-band { position: absolute; left: 0; right: 0; bottom: 0; height: 21px; background: var(--navy); }
</style>
</head>
<body>
  <section class="card card-front">
    <div class="front-lockup">
      <span class="brand-mark"></span>
      <span class="brand-name">K T MASONRY</span>
    </div>
  </section>

  <section class="card card-back">
    <div class="back-lockup">
      <span class="brand-mark"></span>
      <span class="brand-name">K T MASONRY</span>
    </div>

    <div class="person">
      <p class="person-name">DANIEL MERCER</p>
      <p class="person-role">Founder and CEO</p>
      <p class="person-company">K T Masonry Works Ltd</p>
    </div>

    <div class="divider"></div>

    <ul class="contacts">
      <li>
        <svg viewBox="0 0 24 24" aria-hidden="true"><path d="M6.6 10.8a15.1 15.1 0 0 0 6.6 6.6l2.2-2.2a1 1 0 0 1 1-.25 11.4 11.4 0 0 0 3.6.57 1 1 0 0 1 1 1V20a1 1 0 0 1-1 1A17 17 0 0 1 3 4a1 1 0 0 1 1-1h3.5a1 1 0 0 1 1 1 11.4 11.4 0 0 0 .57 3.6 1 1 0 0 1-.25 1z"/></svg>
        <span>000 000 0000</span>
      </li>
      <li>
        <svg viewBox="0 0 24 24" aria-hidden="true"><path d="M7 1h10a2 2 0 0 1 2 2v18a2 2 0 0 1-2 2H7a2 2 0 0 1-2-2V3a2 2 0 0 1 2-2zm0 3v15h10V4z"/></svg>
        <span>000 000 0000</span>
      </li>
      <li>
        <svg viewBox="0 0 24 24" aria-hidden="true"><path d="M2 5h20v14H2zm2 2v.5l8 5 8-5V7z"/></svg>
        <span>info@ktmasonry.com.au</span>
      </li>
    </ul>

    <div class="footer-band"></div>
  </section>
</body>
</html>
```